Business card design for Automotive workshop

We need a business card for a new automotive repair and tyre shop called Keelstone Prime Automotive located in New Zealand. We are a clean, modern and fresh workshop and company.

Front needs to feature logo,
my name:
Marlo Fenwicke (director)

Address:
48 Tarn Lane
Whitianga 3510

Phone: 07 594 2713
Mobile: 027 451 9362
Email: office@keelstoneautomotive.example.nz
Website: keelstoneautomotive.example.nz

Back needs to feature an area to write down appointment details, date and time.

Also feature a list of jobs and work we do such as,
Vehicle Servicing
All Mechanical Repairs
Warrant of Fitness
Tyres & Wheel Alignments
Automotive Diagnostics
Automotive Parts & Supplies

```html
<!DOCTYPE html>
<html lang="en">
<head>
<meta charset="utf-8">
<title>Keelstone Prime Automotive – Business Card</title>
<link rel="stylesheet" href="https://fonts.googleapis.com/css2?family=Arimo:wght@400;700&display=swap">
<style>
  :root {
    --bg: #3a3a3a;
    --card: #030303;
    --red: #e32228;
    --band: #3b3a3a;
    --white: #ffffff;
  }
  * { box-sizing: border-box; margin: 0; padding: 0; }
  html, body { width: 1200px; height: 750px; overflow: hidden; }
  body {
    background: var(--bg);
    font-family: "Arimo", Arial, sans-serif;
    position: relative;
  }
  .card {
    position: absolute;
    top: 186px;
    height: 328px;
    background: var(--card);
    border-radius: 32px;
    overflow: hidden;
  }
  .card--front { left: 38px; width: 558px; }
  .card--back { left: 610px; width: 562px; }
  .card__shapes { position: absolute; inset: 0; width: 100%; height: 100%; }
  .shape--band { fill: var(--band); }
  .shape--red { fill: var(--red); }

  .brand { position: absolute; color: var(--red); font-weight: 700; line-height: 1; }
  .brand__name { display: block; font-size: 25px; letter-spacing: 1px; }
  .brand__sub { display: block; font-size: 11px; letter-spacing: 5px; margin-top: 4px; }
  .card--front .brand { left: 24px; top: 52px; }
  .card--back .brand { left: 0; right: 0; top: 76px; text-align: center; }

  .person { position: absolute; left: 20px; top: 108px; width: 261px; }
  .person__name {
    display: flex; align-items: center; gap: 6px;
    color: var(--red); font-weight: 700; font-size: 21px; word-spacing: 3px;
  }
  .person__role { color: var(--red); font-size: 19px; margin: 2px 0 0 27px; word-spacing: 3px; }
  .person__rule { height: 3px; background: var(--red); margin-top: 3px; }

  .contact { position: absolute; left: 20px; top: 178px; list-style: none; }
  .contact li {
    display: flex; align-items: center; gap: 6px;
    color: var(--red); font-size: 14.5px; height: 21px; word-spacing: 3px;
  }
  .contact li.gap { margin-top: 3px; }
  .icon { width: 16px; height: 16px; flex: none; }
  .icon circle { fill: var(--white); }
  .icon .glyph { fill: var(--card); }

  .services {
    position: absolute; left: 0; right: 0; top: 133px;
    list-style: none; text-align: center;
    color: var(--red); font-size: 14.5px; line-height: 20px; word-spacing: 3px;
  }
  .services li { padding-left: 6px; }

  .appointment { position: absolute; top: 280px; left: 29px; right: 40px; display: flex; gap: 34px; }
  .appointment__field { flex: 1; display: flex; align-items: center; color: var(--red); font-size: 14.5px; }
  .appointment__field::before {
    content: ""; width: 7px; height: 7px; border-radius: 50%; background: var(--red); margin-right: 8px;
  }
  .appointment__line { flex: 1; height: 3px; background: var(--red); margin: 6px 0 0 6px; }
</style>
</head>
<body>

<section class="card card--front" aria-label="Business card front">
  <svg class="card__shapes" viewBox="0 0 698 410" preserveAspectRatio="none" aria-hidden="true">
    <polygon class="shape--band" points="503,0 518,0 438,252 680,410 640,410 418,262"/>
    <polygon class="shape--red" points="518,0 698,0 698,410 680,410 438,252"/>
  </svg>

  <div class="brand">
    <span class="brand__name">KEELSTONE PRIME</span>
    <span class="brand__sub">AUTOMOTIVE</span>
  </div>

  <div class="person">
    <div class="person__name">
      <svg class="icon" style="width:22px;height:22px" viewBox="0 0 16 16" aria-hidden="true">
        <circle cx="8" cy="8" r="8"/>
        <circle class="glyph" cx="8" cy="4.6" r="1.8" style="fill:var(--card)"/>
        <rect class="glyph" x="5.6" y="7" width="4.8" height="6" rx="1"/>
      </svg>
      Marlo Fenwicke
    </div>
    <div class="person__role">(Director)</div>
    <div class="person__rule"></div>
  </div>

  <ul class="contact">
    <li>
      <svg class="icon" viewBox="0 0 16 16" aria-hidden="true"><circle cx="8" cy="8" r="8"/>
        <path class="glyph" d="M5 4h2l1 2.5-1.2 1a6 6 0 0 0 2.7 2.7l1-1.2L13 10v2a1 1 0 0 1-1 1A8 8 0 0 1 4 5a1 1 0 0 1 1-1z"/></svg>
      027 451 9362
    </li>
    <li>
      <svg class="icon" viewBox="0 0 16 16" aria-hidden="true"><circle cx="8" cy="8" r="8"/>
        <path class="glyph" d="M3.5 6.5c0-1.5 9-1.5 9 0v1h-2.2v-1h-4.6v1H3.5z"/>
        <rect class="glyph" x="5" y="8" width="6" height="3.5" rx=".8"/></svg>
      07 594 2713
    </li>
    <li class="gap">
      <svg class="icon" viewBox="0 0 16 16" aria-hidden="true"><circle cx="8" cy="8" r="8"/>
        <rect class="glyph" x="4" y="5.5" width="8" height="5.5" rx=".6"/>
        <path d="M4.3 5.8 8 8.6l3.7-2.8" fill="none" stroke="#fff" stroke-width=".8"/></svg>
      office@keelstoneautomotive.example.nz
    </li>
    <li class="gap">
      <svg class="icon" viewBox="0 0 16 16" aria-hidden="true"><circle cx="8" cy="8" r="8"/>
        <g fill="none" stroke="#030303" stroke-width="1"><circle cx="8" cy="8" r="4.5"/><ellipse cx="8" cy="8" rx="2" ry="4.5"/><path d="M3.5 8h9"/></g></svg>
      keelstoneautomotive.example.nz
    </li>
    <li>
      <svg class="icon" viewBox="0 0 16 16" aria-hidden="true"><circle cx="8" cy="8" r="8"/>
        <path class="glyph" d="M8 3.5 3.5 7.8h1.3V12h2.3V9.5h1.8V12h2.3V7.8h1.3z"/></svg>
      48 Tarn Lane Whitianga 3510
    </li>
  </ul>
</section>

<section class="card card--back" aria-label="Business card back">
  <svg class="card__shapes" viewBox="0 0 702 410" preserveAspectRatio="none" aria-hidden="true">
    <polygon class="shape--band" points="588,0 603,0 537,207 702,313 702,343 517,222"/>
    <polygon class="shape--red" points="603,0 702,0 702,313 537,207"/>
  </svg>

  <div class="brand">
    <span class="brand__name">KEELSTONE PRIME</span>
    <span class="brand__sub">AUTOMOTIVE</span>
  </div>

  <ul class="services">
    <li>Vehicle Servicing</li>
    <li>Warrant of Fitness</li>
    <li>Automotive Diagnostics</li>
    <li>All Mechanical Repairs</li>
    <li>Tyres &amp; Wheel Alignments</li>
    <li>Automotive Parts &amp; Supplies</li>
  </ul>

  <div class="appointment">
    <div class="appointment__field">Date<span class="appointment__line"></span></div>
    <div class="appointment__field">Time<span class="appointment__line"></span></div>
  </div>
</section>

</body>
</html>
```